Military and tactical gear supply company needs web design

We need a web design for a company called U.S. Torvane. We provide quality tactical equipment to military and law enforcement. This is an e-commerce business and we primarily market ourselves on social media. Our key products are backpacks, military-style belts, and tactical flashlights. The gear we sell is not yet widely known about, but is on par with the state-of-the-art products in this field. We want the website to convey the message of quality, durability, and reliability. We use the word "kinetic" because the customers in this field are very "action-oriented" and we would like that idea to be communicated in the web site as well. The primary demographic is men in their 20's-30's, so the web site should have a masculine feel to it. Attached is the logo and color scheme.

```html
<!DOCTYPE html>
<html lang="en">
<head>
<meta charset="utf-8">
<title>U.S. Torvane — Home</title>
<link rel="stylesheet" href="https://fonts.googleapis.com/css2?family=Anton&family=Roboto:wght@400;700&display=swap">
<style>
:root{
  --stage:#000;
  --red:#b3121f;
  --charcoal:#1f1d1f;
  --charcoal-2:#262426;
  --hero-a:#5b5a3c;--hero-b:#3d3a2e;--hero-c:#2a2a22;
}
*{margin:0;padding:0;box-sizing:border-box}
html,body{width:824px;height:1200px;overflow:hidden;background:var(--stage)}
body{position:relative;font-family:"Roboto",Arial,sans-serif}
.page{
  --paper:#fff;--ink:#111;--muted:#444;--nav-ink:#111;--mark:#1a1a1e;--edge:#fff;
  position:absolute;top:30px;width:358px;height:1139px;background:var(--paper);overflow:hidden;color:var(--ink)
}
.page--light{left:40px}
.page--dark{left:419px;--paper:#141214;--ink:#fff;--muted:#cfcfcf;--nav-ink:#fff;--mark:#2f6782;--edge:#141214}
.abs{position:absolute}
.center{left:0;width:100%;text-align:center}
/* nav */
.nav{top:0;left:0;width:100%;height:34px;background:var(--paper)}
.nav__item{top:14px;font-family:"Anton",sans-serif;font-size:5.6px;letter-spacing:.2px;color:var(--nav-ink)}
.nav__item--active{color:var(--red)}
.nav__item--active::after{content:"";position:absolute;left:0;right:0;bottom:-2px;height:.6px;background:var(--red)}
.brand{font-family:"Anton",sans-serif;color:var(--nav-ink);white-space:nowrap;line-height:1}
.brand__url{font-family:"Roboto",sans-serif;font-size:3.6px;color:var(--muted)}
.cart{top:10px;left:295px;width:12px;height:12px;border-radius:50%;background:#111;border:1px solid #111}
.page--dark .cart{background:none;border-color:var(--red)}
.cart svg{position:absolute;left:3px;top:3px}
/* hero */
.hero{top:34px;left:0;width:100%;height:186px;
  background:radial-gradient(ellipse at 75% 40%,#1c1c20 0 18%,transparent 32%),linear-gradient(160deg,var(--hero-a),var(--hero-b) 45%,var(--hero-c))}
.hero__brand{top:96px;left:39px;font-size:19px;color:#e8e8e8;letter-spacing:.5px}
.hero__tagline{top:130px;left:40px;width:135px;text-align:center;font-family:"Anton",sans-serif;font-size:10px;line-height:12px;color:#fff}
.edge{left:0;width:100%}
.edge path{fill:var(--edge)}
/* sections */
.heading{font-family:"Anton",sans-serif;font-size:21px;line-height:1;color:var(--ink);letter-spacing:.2px}
.lede{font-size:4.1px;line-height:6.7px;color:var(--muted)}
.mark-word{top:320px;font-family:"Anton",sans-serif;font-size:78px;line-height:1;color:var(--mark);letter-spacing:2px;font-style:normal}
/* products */
.product{top:500px;width:100px;text-align:center}
.product__img{margin:0 auto;width:40px;height:44px;border-radius:4px}
.product__title{margin-top:6px;font-family:"Anton",sans-serif;font-size:6.4px;color:var(--ink)}
.product__text{margin-top:3px;font-size:3.8px;line-height:6px;color:var(--muted)}
.btn{display:inline-block;margin-top:3px;width:32px;height:8px;border:.7px solid var(--red);border-radius:5px;font-family:"Anton",sans-serif;font-size:3.6px;line-height:6.6px;color:var(--red)}
.divider{top:500px;width:.6px;height:88px;background:#bbb}
/* why */
.why{top:607px;left:0;width:100%;height:183px;background:linear-gradient(180deg,var(--charcoal-2),var(--charcoal))}
.page--dark .why{background:#1c1a1c}
.why .heading{color:#fff}
.feature{top:676px;width:84px;text-align:center}
.feature__title{margin-top:4px;font-family:"Anton",sans-serif;font-size:9px;color:#fff}
.feature__text{margin-top:3px;font-size:3.8px;line-height:5.7px;color:#ddd}
.feature-frame{top:670px;left:136px;width:88px;height:92px;border:1px solid #6d141b}
/* posts */
.post{overflow:hidden}
.post__date{font-family:"Anton",sans-serif;font-size:5px;color:#fff}
.post__title{font-family:"Anton",sans-serif;font-size:6px;line-height:9px;color:#fff;margin-top:4px}
/* footer */
.footer{top:1022px;left:0;width:100%;height:117px;background:var(--charcoal)}
.page--dark .footer{background:#1a181a}
.footer__head{top:1061px;font-family:"Anton",sans-serif;font-size:5px;color:#fff}
.footer__list{top:1073px;list-style:none;font-size:3.2px;line-height:6.5px;color:#aaa}
.email{top:1087px;left:51px;width:95px;height:13px;border:.6px solid #bbb;background:#fff}
.email span{position:absolute;left:5px;top:4px;font-size:4px;font-style:italic;color:#333}
.email b{position:absolute;right:0;top:0;width:32px;height:100%;background:var(--red);color:#fff;font-family:"Anton",sans-serif;font-weight:400;font-size:5px;line-height:12px;text-align:center}
.social{top:1078px;width:6px;height:6px;border-radius:50%;background:#fff}
.legal{font-size:3.2px;line-height:6.5px;color:#aaa}
</style>
</head>
<body>

<!-- ===== LIGHT THEME ===== -->
<section class="page page--light">
  <header class="nav abs">
    <span class="nav__item nav__item--active abs" style="left:52px">HOME</span>
    <span class="nav__item abs" style="left:77px">ABOUT</span>
    <span class="nav__item abs" style="left:103px">PRODUCTS</span>
    <div class="brand abs" style="left:144px;top:11px;font-size:10px">U.S. TORVANE<div class="brand__url" style="text-align:right;margin-top:1px">torvane-gear.com</div></div>
    <span class="nav__item abs" style="left:241px">NEWS</span>
    <span class="nav__item abs" style="left:266px">CONTACT</span>
    <span class="cart abs"><svg width="6" height="6" viewBox="0 0 6 6"><path d="M1 2h4l-.4 3.5H1.4z M2 2V1.4a1 1 0 0 1 2 0V2" fill="none" stroke="#fff" stroke-width=".5"/></svg></span>
  </header>
  <div class="hero abs" role="img" aria-label="Hiker in dark tactical jacket and backpack before a mossy cliff"></div>
  <div class="brand hero__brand abs">U.S. TORVANE<div class="brand__url" style="font-size:7px;color:#ddd;text-align:right;margin-top:2px">torvane-gear.com</div></div>
  <p class="hero__tagline abs">Lorem ipsum dolor sit amet consectetur adipiscing</p>
  <svg class="edge abs" style="top:203px" width="358" height="20" viewBox="0 0 358 20" preserveAspectRatio="none"><path d="M0 12 L14 9 L26 13 L40 8 L58 11 L72 7 L90 12 L108 9 L124 13 L142 8 L160 10 L178 6 L196 11 L214 8 L232 12 L250 7 L268 10 L286 6 L304 9 L322 5 L340 9 L358 4 V20 H0Z"/></svg>

  <h2 class="heading abs center" style="top:244px">ABOUT U.S. TORVANE</h2>
  <p class="lede abs" style="top:274px;left:78px;width:202px;text-align:center">Lorem ipsum dolor sit amet, consectetur adipiscing elit, sed do eiusmod temor incididunt ut labore et dolore magnaaiqt enim ad minied ut perspiciatis unde omnis iste natus error sit voluptatem accusantium doloremque laudantium, totam rem aperiam, eaque ipsa quae ab illo inventore veritatis et quasi architecto beatae vitae dicta sunt explicabo. Nemo enim ipsam voluptatem quia voluptas sit aspernatur aut odit aut fugit</p>
  <div class="mark-word abs center">TORVANE</div>

  <h2 class="heading abs center" style="top:441px">OUR PRODUCTS</h2>
  <p class="lede abs" style="top:471px;left:85px;width:188px;text-align:center">Lorem ipsum dolor sit amet, consectetur adipiscing elit, sed do eiusmod temor incididunt ut labore et dolore magnaaiqt enim ad minied ut perspiciatis unde omnis iste natus error sit voluptatem</p>
  <div class="product abs" style="left:27px"><div class="product__img" role="img" aria-label="Brown hiking backpack" style="background:linear-gradient(160deg,#5a4a44,#2c2624)"></div><div class="product__title">BACKPACKS</div><div class="product__text">Lorem ipsum dolor simeco<br>nsectetur adipiscing</div><span class="btn">VIEW DETAILS</span></div>
  <div class="divider abs" style="left:126px"></div>
  <div class="product abs" style="left:126px"><div class="product__img" role="img" aria-label="Olive canvas military belt with canteen pouch" style="background:linear-gradient(160deg,#7a7d4a,#4f5230)"></div><div class="product__title">MILITARY STYLE BELTS</div><div class="product__text">Lorem ipsum dolor simeco<br>nsectetur adipiscing</div><span class="btn">VIEW DETAILS</span></div>
  <div class="divider abs" style="left:230px"></div>
  <div class="product abs" style="left:232px"><div class="product__img" role="img" aria-label="Tactical flashlight and headlamp set" style="background:linear-gradient(160deg,#3a3a3a,#121212)"></div><div class="product__title">TACTICAL FLASHLIGHTS</div><div class="product__text">Lorem ipsum dolor simeco<br>nsectetur adipiscing</div><span class="btn">VIEW DETAILS</span></div>

  <svg class="edge abs" style="top:596px" width="358" height="14" viewBox="0 0 358 14" preserveAspectRatio="none"><path d="M0 8 L20 5 L38 9 L60 4 L80 8 L104 3 L126 7 L150 4 L174 8 L198 3 L222 7 L246 4 L270 8 L294 3 L318 7 L340 4 L358 7 V14 H0Z" style="fill:#262426"/></svg>
  <div class="why abs">
    <h2 class="heading abs center" style="top:23px">WHY CHOOSE US</h2>
  </div>
  <div class="feature-frame abs"></div>
  <div class="feature abs" style="left:46px"><svg width="28" height="28" viewBox="0 0 28 28"><circle cx="14" cy="12" r="8" fill="none" stroke="#b3121f" stroke-width="1.2"/><path d="M9 18 L6 26 L10 24 L12 27 L14 20 M19 18 L22 26 L18 24 L16 27 L14 20" fill="none" stroke="#b3121f" stroke-width="1"/></svg><div class="feature__title">QUALITY</div><div class="feature__text">Lorem ipsum dolor sit amet, consecte tur adipiscing elit, sed do eiusmod temor incididunt ut labore et dolore magnaal iqt enim ad minim veniamis.</div></div>
  <div class="feature abs" style="left:137px"><svg width="28" height="28" viewBox="0 0 28 28"><path d="M14 3 L24 7 V14 C24 20 19 24 14 26 C9 24 4 20 4 14 V7Z" fill="none" stroke="#b3121f" stroke-width="1.2"/><path d="M14 9 L15.5 13 L19.5 13 L16.3 15.5 L17.5 19.5 L14 17 L10.5 19.5 L11.7 15.5 L8.5 13 L12.5 13Z" fill="#b3121f"/></svg><div class="feature__title">DURABILITY</div><div class="feature__text">Lorem ipsum dolor sit amet, consecte tur adipiscing elit, sed do eiusmod temor incididunt ut labore et dolore magnaal iqt enim ad minim veniamis.</div></div>
  <div class="feature abs" style="left:228px"><svg width="28" height="28" viewBox="0 0 28 28"><circle cx="14" cy="14" r="11" fill="none" stroke="#b3121f" stroke-width="1.2"/><circle cx="14" cy="14" r="7.5" fill="none" stroke="#b3121f" stroke-width="1"/><path d="M14 9.5 V14 L17 16" fill="none" stroke="#b3121f" stroke-width="1"/></svg><div class="feature__title">RELIABILITY</div><div class="feature__text">Lorem ipsum dolor sit amet, consecte tur adipiscing elit, sed do eiusmod temor incididunt ut labore et dolore magnaal iqt enim ad minim veniamis.</div></div>
  <svg class="edge abs" style="top:782px" width="358" height="14" viewBox="0 0 358 14" preserveAspectRatio="none"><path d="M0 6 L22 9 L44 5 L68 10 L92 6 L116 9 L140 4 L164 8 L188 5 L212 9 L236 5 L260 9 L284 4 L308 8 L332 5 L358 8 V14 H0Z"/></svg>

  <h2 class="heading abs center" style="top:810px">LATEST POSTS</h2>
  <p class="lede abs" style="top:838px;left:95px;width:168px;text-align:center">Lorem ipsum dolor sit amet, consectetur adipiscing elit, sed do eiusmod temor incididunt ut labore et dolore magnaaiqt enim ad minied ut perspiciatis unde omnis iste natus</p>
  <article class="post abs" style="left:51px;top:860px;width:160px;height:129px;background:linear-gradient(160deg,#3a3b44,#15161a)" role="img" aria-label="Black tactical pack with flashlight, watch and multitool"><div class="abs" style="left:9px;top:93px"><div class="post__date">July 25 2020</div><div class="post__title">Lorem ipsum dolor sit amet, conse<br>ctetur adipiscing elitedeiusm</div></div></article>
  <article class="post abs" style="left:215px;top:860px;width:94px;height:63px;background:linear-gradient(160deg,#4a3e2c,#151310)" role="img" aria-label="Gloved hand on tactical gear"><div class="abs" style="left:9px;top:25px"><div class="post__date">July 25 2020</div><div class="post__title">Lorem ipsum dolor sit amet<br>conse ctetug elitedeiusm</div></div></article>
  <article class="post abs" style="left:215px;top:926px;width:94px;height:63px;background:linear-gradient(160deg,#2e2e32,#111)" role="img" aria-label="Hand holding a flashlight in the dark"><div class="abs" style="left:9px;top:25px"><div class="post__date">July 25 2020</div><div class="post__title">Lorem ipsum dolor sit amet<br>conse ctetug elitedeiusm</div></div></article>

  <svg class="edge abs" style="top:1012px" width="358" height="14" viewBox="0 0 358 14" preserveAspectRatio="none"><path d="M0 7 L24 4 L48 9 L72 5 L96 9 L120 4 L144 8 L168 5 L192 9 L216 4 L240 8 L264 5 L288 9 L312 4 L336 8 L358 5 V14 H0Z" style="fill:#1f1d1f"/></svg>
  <footer class="footer abs"></footer>
  <div class="brand abs" style="left:51px;top:1064px;font-size:11px;color:#fff">U.S. TORVANE<div class="brand__url" style="text-align:right;color:#bbb;margin-top:1px">torvane-gear.com</div></div>
  <div class="email abs"><span>Email</span><b>SUBMIT</b></div>
  <div class="footer__head abs" style="left:162px">LINKS</div>
  <ul class="footer__list abs" style="left:162px"><li>HOME</li><li>PRODUCTS</li><li>ABOUT US</li><li>CONTACT US</li><li>TERMS &amp; SERVICES</li></ul>
  <div class="footer__head abs" style="left:208px">WE HELP?</div>
  <ul class="footer__list abs" style="left:208px"><li>SHIPPING</li><li>REFUND POLICY</li><li>PRIVACY POLICY</li><li>TERMS OF SERVICE</li><li>FAQS</li></ul>
  <div class="footer__head abs" style="left:258px">FOLLOW US</div>
  <span class="social abs" style="left:258px"></span><span class="social abs" style="left:272px"></span><span class="social abs" style="left:286px"></span><span class="social abs" style="left:300px"></span>
  <p class="legal abs" style="left:258px;top:1090px">© 2020 All Rights Are Reserved.<br>Terms of Use | Privacy Policy</p>
</section>

<!-- ===== DARK THEME ===== -->
<section class="page page--dark">
  <header class="nav abs">
    <span class="nav__item nav__item--active abs" style="left:52px">HOME</span>
    <span class="nav__item abs" style="left:77px">ABOUT</span>
    <span class="nav__item abs" style="left:103px">PRODUCTS</span>
    <div class="brand abs" style="left:144px;top:11px;font-size:10px">U.S. TORVANE<div class="brand__url" style="text-align:right;margin-top:1px">torvane-gear.com</div></div>
    <span class="nav__item abs" style="left:241px">NEWS</span>
    <span class="nav__item abs" style="left:266px">CONTACT</span>
    <span class="cart abs"><svg width="6" height="6" viewBox="0 0 6 6"><path d="M1 2h4l-.4 3.5H1.4z M2 2V1.4a1 1 0 0 1 2 0V2" fill="none" stroke="#b3121f" stroke-width=".5"/></svg></span>
  </header>
  <div class="hero abs" role="img" aria-label="Hiker in dark tactical jacket and backpack before a mossy cliff"></div>
  <div class="brand hero__brand abs">U.S. TORVANE<div class="brand__url" style="font-size:7px;color:#ddd;text-align:right;margin-top:2px">torvane-gear.com</div></div>
  <p class="hero__tagline abs">Lorem ipsum dolor sit amet consectetur adipiscing</p>
  <svg class="edge abs" style="top:203px" width="358" height="20" viewBox="0 0 358 20" preserveAspectRatio="none"><path d="M0 12 L14 9 L26 13 L40 8 L58 11 L72 7 L90 12 L108 9 L124 13 L142 8 L160 10 L178 6 L196 11 L214 8 L232 12 L250 7 L268 10 L286 6 L304 9 L322 5 L340 9 L358 4 V20 H0Z"/></svg>

  <h2 class="heading abs center" style="top:244px">ABOUT U.S. TORVANE</h2>
  <p class="lede abs" style="top:274px;left:78px;width:202px;text-align:center">Lorem ipsum dolor sit amet, consectetur adipiscing elit, sed do eiusmod temor incididunt ut labore et dolore magnaaiqt enim ad minied ut perspiciatis unde omnis iste natus error sit voluptatem accusantium doloremque laudantium, totam rem aperiam, eaque ipsa quae ab illo inventore veritatis et quasi architecto beatae vitae dicta sunt explicabo. Nemo enim ipsam voluptatem quia voluptas sit aspernatur aut odit aut fugit</p>
  <div class="mark-word abs center">TORVANE</div>

  <h2 class="heading abs center" style="top:441px">OUR PRODUCTS</h2>
  <p class="lede abs" style="top:471px;left:85px;width:188px;text-align:center">Lorem ipsum dolor sit amet, consectetur adipiscing elit, sed do eiusmod temor incididunt ut labore et dolore magnaaiqt enim ad minied ut perspiciatis unde omnis iste natus error sit voluptatem</p>
  <div class="product abs" style="left:27px"><div class="product__img" role="img" aria-label="Brown hiking backpack" style="background:linear-gradient(160deg,#5a4a44,#2c2624)"></div><div class="product__title">BACKPACKS</div><div class="product__text">Lorem ipsum dolor simeco<br>nsectetur adipiscing</div><span class="btn">VIEW DETAILS</span></div>
  <div class="divider abs" style="left:126px;background:#ddd"></div>
  <div class="product abs" style="left:126px"><div class="product__img" role="img" aria-label="Olive canvas military belt with canteen pouch" style="background:linear-gradient(160deg,#7a7d4a,#4f5230)"></div><div class="product__title">MILITARY STYLE BELTS</div><div class="product__text">Lorem ipsum dolor simeco<br>nsectetur adipiscing</div><span class="btn">VIEW DETAILS</span></div>
  <div class="divider abs" style="left:230px;background:#ddd"></div>
  <div class="product abs" style="left:232px"><div class="product__img" role="img" aria-label="Tactical flashlight and headlamp set" style="background:linear-gradient(160deg,#3a3a3a,#121212)"></div><div class="product__title">TACTICAL FLASHLIGHTS</div><div class="product__text">Lorem ipsum dolor simeco<br>nsectetur adipiscing</div><span class="btn">VIEW DETAILS</span></div>

  <div class="why abs">
    <h2 class="heading abs center" style="top:23px">WHY CHOOSE US</h2>
  </div>
  <div class="feature-frame abs"></div>
  <div class="feature abs" style="left:46px"><svg width="28" height="28" viewBox="0 0 28 28"><circle cx="14" cy="12" r="8" fill="none" stroke="#b3121f" stroke-width="1.2"/><path d="M9 18 L6 26 L10 24 L12 27 L14 20 M19 18 L22 26 L18 24 L16 27 L14 20" fill="none" stroke="#b3121f" stroke-width="1"/></svg><div class="feature__title">QUALITY</div><div class="feature__text">Lorem ipsum dolor sit amet, consecte tur adipiscing elit, sed do eiusmod temor incididunt ut labore et dolore magnaal iqt enim ad minim veniamis.</div></div>
  <div class="feature abs" style="left:137px"><svg width="28" height="28" viewBox="0 0 28 28"><path d="M14 3 L24 7 V14 C24 20 19 24 14 26 C9 24 4 20 4 14 V7Z" fill="none" stroke="#b3121f" stroke-width="1.2"/><path d="M14 9 L15.5 13 L19.5 13 L16.3 15.5 L17.5 19.5 L14 17 L10.5 19.5 L11.7 15.5 L8.5 13 L12.5 13Z" fill="#b3121f"/></svg><div class="feature__title">DURABILITY</div><div class="feature__text">Lorem ipsum dolor sit amet, consecte tur adipiscing elit, sed do eiusmod temor incididunt ut labore et dolore magnaal iqt enim ad minim veniamis.</div></div>
  <div class="feature abs" style="left:228px"><svg width="28" height="28" viewBox="0 0 28 28"><circle cx="14" cy="14" r="11" fill="none" stroke="#b3121f" stroke-width="1.2"/><circle cx="14" cy="14" r="7.5" fill="none" stroke="#b3121f" stroke-width="1"/><path d="M14 9.5 V14 L17 16" fill="none" stroke="#b3121f" stroke-width="1"/></svg><div class="feature__title">RELIABILITY</div><div class="feature__text">Lorem ipsum dolor sit amet, consecte tur adipiscing elit, sed do eiusmod temor incididunt ut labore et dolore magnaal iqt enim ad minim veniamis.</div></div>

  <h2 class="heading abs center" style="top:810px">LATEST POSTS</h2>
  <p class="lede abs" style="top:838px;left:95px;width:168px;text-align:center">Lorem ipsum dolor sit amet, consectetur adipiscing elit, sed do eiusmod temor incididunt ut labore et dolore magnaaiqt enim ad minied ut perspiciatis unde omnis iste natus</p>
  <article class="post abs" style="left:51px;top:860px;width:160px;height:129px;background:linear-gradient(160deg,#3a3b44,#15161a)" role="img" aria-label="Black tactical pack with flashlight, watch and multitool"><div class="abs" style="left:9px;top:93px"><div class="post__date">July 25 2020</div><div class="post__title">Lorem ipsum dolor sit amet, conse<br>ctetur adipiscing elitedeiusm</div></div></article>
  <article class="post abs" style="left:215px;top:860px;width:94px;height:63px;background:linear-gradient(160deg,#4a3e2c,#151310)" role="img" aria-label="Gloved hand on tactical gear"><div class="abs" style="left:9px;top:25px"><div class="post__date">July 25 2020</div><div class="post__title">Lorem ipsum dolor sit amet<br>conse ctetug elitedeiusm</div></div></article>
  <article class="post abs" style="left:215px;top:926px;width:94px;height:63px;background:linear-gradient(160deg,#2e2e32,#111)" role="img" aria-label="Hand holding a flashlight in the dark"><div class="abs" style="left:9px;top:25px"><div class="post__date">July 25 2020</div><div class="post__title">Lorem ipsum dolor sit amet<br>conse ctetug elitedeiusm</div></div></article>

  <footer class="footer abs"></footer>
  <div class="brand abs" style="left:51px;top:1064px;font-size:11px;color:#fff">U.S. TORVANE<div class="brand__url" style="text-align:right;color:#bbb;margin-top:1px">torvane-gear.com</div></div>
  <div class="email abs"><span>Email</span><b>SUBMIT</b></div>
  <div class="footer__head abs" style="left:162px">LINKS</div>
  <ul class="footer__list abs" style="left:162px"><li>HOME</li><li>PRODUCTS</li><li>ABOUT US</li><li>CONTACT US</li><li>TERMS &amp; SERVICES</li></ul>
  <div class="footer__head abs" style="left:208px">WE HELP?</div>
  <ul class="footer__list abs" style="left:208px"><li>SHIPPING</li><li>REFUND POLICY</li><li>PRIVACY POLICY</li><li>TERMS OF SERVICE</li><li>FAQS</li></ul>
  <div class="footer__head abs" style="left:258px">FOLLOW US</div>
  <span class="social abs" style="left:258px"></span><span class="social abs" style="left:272px"></span><span class="social abs" style="left:286px"></span><span class="social abs" style="left:300px"></span>
  <p class="legal abs" style="left:258px;top:1090px">© 2020 All Rights Are Reserved.<br>Terms of Use | Privacy Policy</p>
</section>

</body>
</html>
```